Business card design for holistic health care clinic

We need a double-sided business card design for our holistic health care clinic that integrates our logo design and also its color scheme. My business is called Valmira. It is an integrative medicine clinic. You have already done the logo for me. Please ensure an elegant and upscale design that is not cluttered, but still has all the necessary information (please see below for details).

Target Market(s)

Wellness, fitness, rehabilitation for educated, well-traveled open-minded clients who are focused on natural, organic, balanced and preventive healthcare and lifestyle.

Industry/Entity Type

Medical

Contact Information for Business Card

Modern, clean.

Number of Pages Required

1 page

Font styles to use
Serif
Sans Serif

Colors

Designer to choose colors to be used in the design.

Requirements
Must have
• Logo on one side, all other information on the other side.
• Other information should include:
• Tobias Wrenfeld - DOE, CPT, LMT
• 4100 East Marrow Drive
• Austin, TX 78119
• 512 555 0148
• 818 555 0192
• info@ValmiraHealth.example
• t.wrenfeld@ValmiraHealth.example
Nice to have
• Darker background on front - but not totally black - shaded/dark gray.

```html
<!DOCTYPE html>
<html lang="en">
<head>
<meta charset="utf-8">
<title>Valmira – Business Card</title>
<link rel="stylesheet" href="https://fonts.googleapis.com/css2?family=Roboto:wght@400;700&family=Roboto+Condensed:ital,wght@0,700;1,700&display=swap">
<style>
  :root {
    --backdrop: #5a4a3c;
    --card-white: #f7f7f7;
    --brand-blue: #0a8ec9;
    --band-gray: #a9abad;
    --rule-gray: #8c8c8c;
    --text-dark: #454545;
    --white: #ffffff;
  }
  html, body {
    margin: 0;
    padding: 0;
    width: 1200px;
    height: 960px;
    overflow: hidden;
    background: var(--backdrop);
  }
  .canvas {
    position: relative;
    width: 1200px;
    height: 960px;
  }
  .card {
    position: absolute;
    width: 600px;
    height: 342px;
    border-radius: 22px;
    overflow: hidden;
  }
  .card-front {
    left: 314px;
    top: 114px;
    background: var(--card-white);
  }
  .card-back {
    left: 311px;
    top: 473px;
    height: 341px;
    background: var(--brand-blue);
  }
  .brand-name {
    position: absolute;
    margin: 0;
    font-family: "Roboto", Arial, sans-serif;
    font-weight: 700;
    letter-spacing: 1px;
    line-height: 1;
  }
  .card-front .brand-name {
    right: 35px;
    top: 78px;
    font-size: 50px;
    color: var(--brand-blue);
  }
  .card-back .brand-name {
    left: 338px;
    top: 200px;
    font-size: 46px;
    color: var(--white);
  }
  .person {
    position: absolute;
    left: 33px;
    top: 176px;
    margin: 0;
    font-family: "Roboto Condensed", "Arial Narrow", sans-serif;
    font-weight: 700;
    font-size: 21px;
    color: var(--brand-blue);
    line-height: 1;
  }
  .person .credentials {
    font-size: 13px;
  }
  .divider {
    position: absolute;
    left: 35px;
    top: 211px;
    width: 530px;
    height: 1px;
    background: var(--rule-gray);
  }
  .contact-list {
    position: absolute;
    left: 35px;
    top: 227px;
    margin: 0;
    padding: 0;
    list-style: none;
    font-family: "Roboto", Arial, sans-serif;
    font-size: 14.5px;
    color: var(--text-dark);
  }
  .contact-list li {
    display: flex;
    align-items: center;
    height: 19px;
  }
  .contact-list svg {
    width: 13px;
    height: 13px;
    margin-right: 9px;
    fill: var(--brand-blue);
  }
  .address {
    position: absolute;
    right: 35px;
    top: 246px;
    margin: 0;
    font-style: normal;
    text-align: right;
    font-family: "Roboto", Arial, sans-serif;
    font-size: 14.5px;
    line-height: 19px;
    color: var(--text-dark);
  }
  .front-bands {
    position: absolute;
    left: 0;
    top: 0;
    width: 600px;
    height: 342px;
  }
  .website {
    position: absolute;
    right: 30px;
    top: 314px;
    margin: 0;
    font-family: "Roboto", Arial, sans-serif;
    font-size: 14.5px;
    letter-spacing: 1.2px;
    color: var(--white);
  }
  .tagline {
    position: absolute;
    left: 341px;
    top: 284px;
    margin: 0;
    font-family: "Roboto Condensed", "Arial Narrow", sans-serif;
    font-weight: 700;
    font-style: italic;
    font-size: 16px;
    color: var(--white);
  }
</style>
</head>
<body>
<main class="canvas">

  <section class="card card-front" aria-label="Business card front">
    <svg class="front-bands" viewBox="0 0 600 342" aria-hidden="true">
      <polygon points="0,319 340,319 333,330 0,330" fill="var(--band-gray)"/>
      <rect x="0" y="331" width="600" height="11" fill="var(--brand-blue)"/>
      <polygon points="348,304 600,304 600,342 326,342" fill="var(--brand-blue)"/>
    </svg>

    <p class="brand-name">VALMIRA</p>

    <h1 class="person">TOBIAS WRENFELD <span class="credentials">- DOE, CPT, LMT</span></h1>
    <div class="divider"></div>

    <ul class="contact-list">
      <li>
        <svg viewBox="0 0 24 24" aria-hidden="true"><path d="M6.6 10.8c1.4 2.8 3.8 5.1 6.6 6.6l2.2-2.2c.3-.3.7-.4 1-.2 1.1.4 2.3.6 3.6.6.6 0 1 .4 1 1V20c0 .6-.4 1-1 1C10.6 21 3 13.4 3 4c0-.6.4-1 1-1h3.5c.6 0 1 .4 1 1 0 1.3.2 2.5.6 3.6.1.3 0 .7-.2 1z"/></svg>
        512 555 0148
      </li>
      <li>
        <svg viewBox="0 0 24 24" aria-hidden="true"><path d="M7 1h10c1.1 0 2 .9 2 2v18c0 1.1-.9 2-2 2H7c-1.1 0-2-.9-2-2V3c0-1.1.9-2 2-2zm0 3v14h10V4H7zm5 15.5a1 1 0 1 0 0 2 1 1 0 0 0 0-2z"/></svg>
        818 555 0192
      </li>
      <li>
        <svg viewBox="0 0 24 24" aria-hidden="true"><path d="M2 5h20v14H2V5zm2 2v.5l8 5 8-5V7H4zm0 2.8V17h16V9.8l-8 5-8-5z"/></svg>
        t.wrenfeld@ValmiraHealth.example
      </li>
    </ul>

    <address class="address">4100 East Marrow Drive<br>Austin, TX 78119</address>

    <p class="website">www.ValmiraHealth.example</p>
  </section>

  <section class="card card-back" aria-label="Business card back">
    <p class="brand-name">VALMIRA</p>
    <p class="tagline">helping the body help itself</p>
  </section>

</main>
</body>
</html>
```